Supplement Brand Product Labels

Product Label for Supplement Brand

Protein Powder Label (2 x different flavours)

Neon Colours / Skull / Spooky
Refer to pictures below, they are the look we are wanting to go with but put our touch to it aswell.

Target Market(s)

Fitness

Industry/Entity Type

Supplement Brand

Colors
0054AA
0677BA
7BADD7
CADEEF
E8F1F8
0094D4
00A9DD
6FCCEA
C7EBF8
E9F6FB
00AB8E
00BBA5
67D7C9
C6EFE9
E9F9F6
59FF00
82FF00
B8FF75
E3FFCB
F4FFEA
FFF300
FFF600
FEFA6F
FFFEC7
FFFEE8
FFC000
F8CF3A
FAE287
FDF2CF
FEFAEE
F0912C
F2A743
F7CA91
FBE8D2
FDF5EE
EE7325
F08F49
F5BC92
FAE3D3
FDF4ED
EB3D1F
EC4F4E
F09395
F8D3D4
FCEDEE
E54698
E96AAD
F1A4CE
F9D9EA
FCEFF6
A7469A
B969AE
D3A5CF
EDDBEB
F8F0F9
6B429C
8869AF
B7A5CE
E3DAEB
F3F0F8

Requirements
Nice to have
• Skull, Neon Colours, Abstract, Barbell, Lighting Bolt, Flames, Spooky

```html
<!DOCTYPE html>
<html lang="en">
<head>
<meta charset="utf-8">
<title>Forgeline Supps – Protein Label Back Panel</title>
<link href="https://fonts.googleapis.com/css2?family=Lato:wght@400;700;900&family=Arvo:wght@700&family=Archivo+Black&family=Anton&display=swap" rel="stylesheet">
<style>
  :root {
    --bg: #000000;
    --ink: #ffffff;
    --panel: #ffffff;
    --panel-ink: #111111;
    --neon: #59ff00;
  }
  * { margin: 0; padding: 0; box-sizing: border-box; }
  html, body { width: 884px; height: 1200px; overflow: hidden; background: var(--bg); }
  .label {
    position: relative; width: 884px; height: 1200px; background: var(--bg);
    color: var(--ink); font-family: "Lato", sans-serif; font-size: 15.5px;
  }
  .abs { position: absolute; }

  /* Nutrition panel */
  .nutrition {
    left: 27px; top: 57px; width: 513px; height: 412px;
    background: var(--panel); color: var(--panel-ink);
  }
  .nutrition .head { font-weight: 700; font-size: 12.8px; line-height: 17px; top: 9px; white-space: nowrap; }
  .nutrition .head.serve { left: 11px; }
  .nutrition .head.col1 { left: 214px; width: 140px; text-align: center; }
  .nutrition .head.col2 { left: 370px; width: 140px; text-align: center; }
  .nutrition .row { left: 0; width: 513px; height: 22px; line-height: 22px; }
  .nutrition .row span { position: absolute; }
  .nutrition .name { left: 11px; }
  .nutrition .row.sub .name { left: 23px; }
  .nutrition .v1 { right: 207px; }
  .nutrition .v2 { right: 51px; }

  /* Amino acids */
  .amino-title {
    left: 560px; top: 62px; width: 288px; text-align: right; white-space: nowrap;
    font-family: "Anton", sans-serif; font-weight: 400; font-size: 22px; line-height: 28px; letter-spacing: -0.2px;
  }
  .amino-head, .amino-row { left: 609px; width: 239px; height: 22px; line-height: 22px; }
  .amino-head { font-weight: 700; font-size: 13px; top: 103px; }
  .amino-head span:last-child, .amino-row span:last-child { position: absolute; right: 0; }

  /* Text sections */
  .section-title { left: 38px; font-family: "Arvo", serif; font-weight: 700; font-size: 22px; line-height: 28px; }
  .copy { left: 38px; width: 485px; line-height: 24.4px; white-space: nowrap; }
  .line-full { display: block; text-align: justify; text-align-last: justify; white-space: normal; }
  .disclaimer { left: 42px; width: 808px; top: 884px; line-height: 24.4px; }
  .disclaimer .line { display: block; }
  .store { left: 42px; top: 996px; font-weight: 900; font-size: 15.5px; }

  /* Brand block */
  .brand { left: 46px; top: 1046px; display: flex; align-items: center; gap: 8px; }
  .brand .mark { width: 22px; height: 22px; background: var(--neon); }
  .brand .name { font-weight: 900; font-size: 30px; line-height: 34px; color: var(--ink); }
  .web { left: 56px; top: 1112px; font-weight: 900; font-size: 13.5px; }
  .address { left: 47px; top: 1132px; font-weight: 900; font-size: 10.5px; letter-spacing: -0.3px; }

  .origin { left: 342px; top: 1085px; display: flex; align-items: center; gap: 5px; }
  .origin .map { width: 33px; height: 31px; background: var(--neon); border-radius: 45% 55% 50% 40%; }
  .origin .text { font-family: "Archivo Black", sans-serif; font-size: 14px; line-height: 14px; color: var(--ink); }

  .blank-box { left: 585px; top: 979px; width: 261px; height: 191px; background: var(--panel); border: 2px solid #2a2a2a; }
</style>
</head>
<body>
<main class="label">

  <section class="nutrition abs" aria-label="Nutrition information">
    <div class="abs head serve">12.5 Serving Per 1kg Packet<br>80 grams Per Serve</div>
    <div class="abs head col1">Average Quantity<br>Per Serving</div>
    <div class="abs head col2">Average Quantity<br>Per 100g</div>
    <div class="abs row" style="top:72px"><span class="name">Energy (KJ)</span><span class="v1">1286</span><span class="v2">1608</span></div>
    <div class="abs row" style="top:121px"><span class="name">Protein (G)</span><span class="v1">24.3</span><span class="v2">30.4</span></div>
    <div class="abs row" style="top:170px"><span class="name">Fat, Total (G)</span><span class="v1">1.7</span><span class="v2">2.1</span></div>
    <div class="abs row sub" style="top:218px"><span class="name">Saturated (G)</span><span class="v1">1.1</span><span class="v2">1.3</span></div>
    <div class="abs row" style="top:268px"><span class="name">Carbohydrates (G)</span><span class="v1">47.6</span><span class="v2">59.5</span></div>
    <div class="abs row sub" style="top:316px"><span class="name">Sugar (G)</span><span class="v1">3.5</span><span class="v2">4.4</span></div>
    <div class="abs row" style="top:365px"><span class="name">Sodium (MG)</span><span class="v1">68</span><span class="v2">85</span></div>
  </section>

  <h2 class="abs amino-title">Typical Amino Acid Profile</h2>
  <div class="abs amino-head"><span>Amino Acid</span><span>MG/100G</span></div>
  <div class="abs amino-row" style="top:142px"><span>Alanine (mg)</span><span>1619</span></div>
  <div class="abs amino-row" style="top:181px"><span>Arginine (mg)</span><span>920</span></div>
  <div class="abs amino-row" style="top:220px"><span>Aspartic Acid (mg)</span><span>3564</span></div>
  <div class="abs amino-row" style="top:258px"><span>Cystine (mg)</span><span>771</span></div>
  <div class="abs amino-row" style="top:297px"><span>Glutamic Acid (mg)</span><span>5863</span></div>
  <div class="abs amino-row" style="top:336px"><span>Glycine (mg)</span><span>620</span></div>
  <div class="abs amino-row" style="top:374px"><span>Histidine (mg)</span><span>628</span></div>
  <div class="abs amino-row" style="top:413px"><span>Isoleucine (mg)</span><span>1861</span></div>
  <div class="abs amino-row" style="top:452px"><span>Leucine (mg)</span><span>3480</span></div>
  <div class="abs amino-row" style="top:490px"><span>Lysine (mg)</span><span>2913</span></div>
  <div class="abs amino-row" style="top:529px"><span>Methionine (mg)</span><span>792</span></div>
  <div class="abs amino-row" style="top:568px"><span>Phenylalanine (mg)</span><span>1154</span></div>
  <div class="abs amino-row" style="top:606px"><span>Proline (mg)</span><span>2400</span></div>
  <div class="abs amino-row" style="top:645px"><span>Serine (mg)</span><span>1803</span></div>
  <div class="abs amino-row" style="top:684px"><span>Threonine (mg)</span><span>2238</span></div>
  <div class="abs amino-row" style="top:722px"><span>Tryptophan (mg)</span><span>529</span></div>
  <div class="abs amino-row" style="top:761px"><span>Tyrosine (mg)</span><span>1112</span></div>
  <div class="abs amino-row" style="top:800px"><span>Valine (mg)</span><span>1759</span></div>

  <h3 class="abs section-title" style="top:504px">Ingredients</h3>
  <p class="abs copy" style="top:539px">Maltodextrin, Whey Protein Concentrate, Milk Protein Isolate,<br>Whey Protein Isolate, Branch Chain Amino Acids, Albumin,<br>Wheaten Cornflour, Wholemeal Flour, Cocoa, Flavour, Sucralose.</p>

  <h3 class="abs section-title" style="top:646px">Allergens</h3>
  <p class="abs copy" style="top:679px">Egg, Milk, Soy, Wheat, Gluten.</p>

  <h3 class="abs section-title" style="top:736px">Directions Of Use</h3>
  <p class="abs copy" style="top:768px"><span class="line-full">Mix 2 heaped scoop (40 grams) with 250ml of water or milk and</span>consume immediately. For optimal results, consume 2 – 3 times<br>per day.</p>

  <p class="abs disclaimer">
    <span class="line line-full">Formulated supplementary sports food. Not suitable for children under 15 years of age or pregnant women.</span>
    <span class="line line-full">Should only be used under medical or dietetic supervision. This product is not a sole source of nutrition and should</span>
    <span class="line">be consumed in conjunction with a nutritious diet and appropriate physical training or exercise program.</span>
  </p>

  <p class="abs store">Store in a cool dry place out of direct sunlight.</p>

  <div class="abs brand"><span class="mark"></span><span class="name">Forgeline</span></div>
  <p class="abs web">www.forgelinesupps.com</p>
  <p class="abs address">PO BOX 118, Northvale QLD 4999</p>

  <div class="abs origin">
    <div class="map" role="img" aria-label="Map outline of Australia"></div>
    <div class="text">MADE IN<br>AUSTRALIA</div>
  </div>

  <div class="abs blank-box"></div>
</main>
</body>
</html>
```